Low Testosterone Center Postcard Design

I need a jumbo direct mail marketing postcard for my men's low testosterone center. We evaluate and treat men with symptoms related to low testosterone. See my website www.oakridgewellclinic.com for more info on the symptoms of low testosterone and the benefits from bio identical replacement therapy. We have physician oversight for our program. Images and documents are available on my website.

Industry/Entity Type

Marketing

```html
<!DOCTYPE html>
<html lang="en">
<head>
<meta charset="utf-8">
<title>Oakridge Well Clinic Postcard</title>
<link rel="stylesheet" href="https://fonts.googleapis.com/css2?family=Jost:wght@300;400;500;600;700&display=swap">
<style>
  :root {
    --backdrop: #6b6b6b;
    --brand-blue: #0b62ae;
    --brand-navy: #0f1b3d;
    --accent-yellow: #f6bd1c;
    --white: #ffffff;
    --sky-top: #bfe3f6;
    --sky-mid: #e9f4fb;
    --sea: #3cb4d8;
  }
  * { margin: 0; padding: 0; box-sizing: border-box; }
  html, body { width: 1200px; height: 809px; overflow: hidden; }
  body { background: var(--backdrop); font-family: "Jost", sans-serif; color: var(--white); }
  .postcard { position: absolute; left: 50px; top: 50px; width: 1100px; height: 708px; overflow: hidden; background: var(--brand-blue); }
  .postcard-shapes { position: absolute; inset: 0; }
  .copy { position: absolute; left: 32px; top: 0; width: 520px; }
  .eyebrow { position: absolute; top: 38px; font-size: 27px; font-weight: 600; letter-spacing: .3px; white-space: nowrap; }
  .headline { position: absolute; top: 68px; font-size: 70px; font-weight: 700; line-height: 68px; letter-spacing: -.5px; white-space: nowrap; }
  .headline .accent { color: var(--accent-yellow); }
  .subhead { position: absolute; top: 230px; font-size: 24.5px; font-weight: 300; line-height: 30px; text-transform: uppercase; white-space: nowrap; }
  .body-copy { position: absolute; top: 344px; width: 410px; font-size: 16px; font-weight: 400; line-height: 22px; }
  .body-copy strong { font-weight: 600; }
  .cta-lead { position: absolute; top: 540px; font-size: 17px; font-weight: 500; color: var(--accent-yellow); white-space: nowrap; }
  .cta-main { position: absolute; top: 562px; font-size: 24px; font-weight: 600; color: var(--accent-yellow); white-space: nowrap; }
  .phone { position: absolute; top: 600px; left: 4px; font-size: 43px; font-weight: 500; letter-spacing: 1px; white-space: nowrap; }
  .website { position: absolute; top: 653px; left: 28px; font-size: 18px; font-weight: 500; color: var(--accent-yellow); white-space: nowrap; }
  .clinic-mark { position: absolute; right: 18px; bottom: 28px; width: 190px; text-align: center; }
  .clinic-mark .dot { width: 74px; height: 74px; border-radius: 50%; background: var(--accent-yellow); margin: 0 auto 14px; }
  .clinic-mark .name { font-size: 19px; font-weight: 500; line-height: 22px; text-transform: uppercase; }
</style>
</head>
<body>
  <div class="postcard">
    <svg class="postcard-shapes" width="1100" height="708" viewBox="0 0 1100 708">
      <defs>
        <linearGradient id="photoTone" x1="0" y1="0" x2="0.3" y2="1">
          <stop offset="0" stop-color="var(--sky-top)"/>
          <stop offset="0.45" stop-color="var(--sky-mid)"/>
          <stop offset="0.7" stop-color="#f4f7f8"/>
          <stop offset="1" stop-color="var(--sea)"/>
        </linearGradient>
      </defs>
      <polygon points="650,0 1100,0 1100,708 350,708" fill="url(#photoTone)" role="img" aria-label="Photo of a smiling couple in white clothing at the beach, woman riding piggyback on the man"/>
      <polygon points="1100,125 1100,708 850,708" fill="var(--brand-navy)"/>
      <line x1="650" y1="0" x2="350" y2="708" stroke="var(--white)" stroke-width="4"/>
      <line x1="1100" y1="122" x2="848" y2="708" stroke="var(--white)" stroke-width="4"/>
    </svg>

    <div class="copy">
      <p class="eyebrow">TRUSTED CENTER FOR</p>
      <h1 class="headline">TREATING <span class="accent">LOW</span><br>TESTOSTERONE</h1>
      <p class="subhead">Helping men change their lives<br>and regain their confidence for<br>over 20 years</p>
      <p class="body-copy">The <strong>Oakridge Well Clinic</strong> is to diagnose and treat men with symptoms of low testosterone, otherwise known as hypogonadism in a quick, efficient, inexpensive and safe manner. We believe that testosterone replacement therapy can improve overall quality of life and can be done very safely in the comfort of an office whose specialty is men’s health.</p>
      <p class="cta-lead">Make an Appointment with Us and</p>
      <p class="cta-main">CHANGE YOUR LIFE TODAY!</p>
      <p class="phone">555-264-0187</p>
      <p class="website">www.oakridgewellclinic.com</p>
    </div>

    <div class="clinic-mark">
      <div class="dot"></div>
      <p class="name">Oakridge<br>Well Clinic</p>
    </div>
  </div>
</body>
</html>
```